Diverse, up-scale salon needs eye-catching, unique business cards.

We are looking for a unique business card design for our stylist but that can also be multi functional and used for appointment reminder and referrals. I will need a design in a format that I can modify names and titles going forward. In the past we have had a dark background with the logo on one side, and stylist and contact information on the other but we are open to all ideas. I have included our mission statement as well as branded colors below. The statement doesn't need to go on the card, it's just a reference for target market. We need space for the stylists name, title, instagram handle and then the salons phone number, website and address. I am also open to adding a spot for a qr code linked to the stylist instagram or the salon booking link.

primary brand colors:
#333333 #233415 #36502a #93874a #000000
Mission statement:
Vessolin Hair Studio, a high-end salon located in the lively Downtown Farmington, Michigan, is committed to providing exceptional services in a welcoming and relaxed environment to meet the needs of our diverse clientele.
Our salon specializes in contemporary custom haircuts, coloring, extensions, and barbering and beard grooming services. Our team of skilled stylists is passionate and inventive in their hair styling techniques. At the heart of our salon are values centered on quality, innovation, creativity, and above all, comfort. These core values are evident in every appointment across our customizable array of services.
Our goal is to establish a benchmark for exceptional hair care for every human.
Website: www.vessolinhairstudio.example
instagram: @vessolinhairstudio
address: 41782 Pelham Crest Rd, Brennford Vale
phone: 555-613-4087

Industry/Entity Type

Hair Salon

Contact Information for Business Card

Stylist name, title, phone, instagram, website, address, (optional qr code)

Requirements
Should not have
• Does not need mission statement on the card.

```html
<!DOCTYPE html>
<html lang="en">
<head>
<meta charset="utf-8">
<title>Vessolin Hair Studio – Business Card</title>
<link rel="stylesheet" href="https://fonts.googleapis.com/css2?family=Cinzel:wght@500&family=Montserrat:wght@400;600&display=swap">
<style>
  :root{
    --scene-bg:#3b3b3b;
    --card-black:#141414;
    --card-black-soft:#1b1b1b;
    --gold:#93874a;
    --gold-light:#a89a55;
    --text-white:#f2f2f2;
  }
  *{box-sizing:border-box;margin:0;padding:0}
  html,body{width:1200px;height:801px;overflow:hidden}
  body{
    background:radial-gradient(ellipse at 50% 45%,#444 0%,var(--scene-bg) 70%);
    font-family:"Montserrat",sans-serif;
    display:flex;align-items:center;justify-content:center;gap:48px;
  }
  .card{
    width:520px;height:297px;
    background:var(--card-black);
    border:2px solid var(--gold);
    position:relative;
    box-shadow:0 18px 40px rgba(0,0,0,.45);
    display:flex;
  }
  /* contact side */
  .card-front .brand-panel{
    width:50%;display:flex;align-items:center;justify-content:center;gap:10px;
    padding:0 12px;
  }
  .brand-dot{width:14px;height:14px;border-radius:50%;background:var(--gold);flex:none}
  .brand-name{
    font-family:"Montserrat",sans-serif;font-weight:600;
    color:var(--gold);font-size:17px;letter-spacing:2px;text-transform:uppercase;
    white-space:nowrap;
  }
  .card-front .brand-name{font-size:13px;letter-spacing:1.5px}
  .card-front .brand-dot{width:12px;height:12px}
  .divider{width:1px;background:var(--gold);margin:62px 0;flex:none}
  .contact-panel{
    width:50%;padding:58px 0 0 28px;color:var(--text-white);
  }
  .stylist-name{
    font-family:"Cinzel",serif;font-weight:500;color:var(--gold-light);
    font-size:24px;letter-spacing:1px;line-height:1;
  }
  .stylist-title{font-size:13px;margin-top:6px}
  .address{font-size:12px;line-height:1.45;margin-top:18px}
  .contact-list{list-style:none;margin-top:16px;font-size:12px;line-height:1.75}
  .contact-list li{display:flex;align-items:center;gap:8px;white-space:nowrap}
  .contact-list svg{width:11px;height:11px;flex:none}
  /* logo side */
  .card-back{align-items:center;justify-content:center;overflow:hidden}
  .pattern-field{
    position:absolute;inset:0;
    background:linear-gradient(115deg,#0c0c0c 0%,var(--card-black-soft) 45%,#2a2a2a 100%);
  }
  .back-brand{position:relative;display:flex;align-items:center;gap:12px}
  .back-brand .brand-dot{width:18px;height:18px}
  .back-brand .brand-name{font-size:22px;letter-spacing:3px}
</style>
</head>
<body>
  <section class="card card-front">
    <div class="brand-panel">
      <span class="brand-dot"></span>
      <span class="brand-name">Vessolin Hair Studio</span>
    </div>
    <div class="divider"></div>
    <div class="contact-panel">
      <h1 class="stylist-name">MARISOL</h1>
      <p class="stylist-title">President</p>
      <p class="address">41782 Pelham Crest Rd<br>Brennford Vale</p>
      <ul class="contact-list">
        <li>
          <svg viewBox="0 0 24 24" aria-hidden="true"><path fill="var(--gold)" d="M6.6 10.8a15.1 15.1 0 0 0 6.6 6.6l2.2-2.2a1 1 0 0 1 1-.25 11.4 11.4 0 0 0 3.6.57 1 1 0 0 1 1 1V20a1 1 0 0 1-1 1A17 17 0 0 1 3 4a1 1 0 0 1 1-1h3.5a1 1 0 0 1 1 1c0 1.25.2 2.45.57 3.57a1 1 0 0 1-.25 1z"/></svg>
          555-613-4087
        </li>
        <li>
          <svg viewBox="0 0 24 24" aria-hidden="true"><circle cx="12" cy="12" r="9" fill="none" stroke="var(--gold)" stroke-width="3"/></svg>
          @vessolinhairstudio
        </li>
        <li>
          <svg viewBox="0 0 24 24" aria-hidden="true"><circle cx="12" cy="12" r="10" fill="var(--gold)"/></svg>
          www.vessolinhairstudio.example
        </li>
      </ul>
    </div>
  </section>

  <section class="card card-back">
    <div class="pattern-field" role="img" aria-label="Tonal repeating monogram pattern in black gloss on black"></div>
    <div class="back-brand">
      <span class="brand-dot"></span>
      <span class="brand-name">Vessolin Hair Studio</span>
    </div>
  </section>
</body>
</html>
```